Hearthside Lending Relief

Please help us give our website a remake or a FACELIFT. It is not very good but it says what we need it to say. But the design is terrible.
I would like our new design font and logo to be used as the theme.

I also want more photos on the site.

I also want consistency with the pages so they look clean.

We want the professionals to do this, let's see what you got!

Thank you!
Updates

Project Deadline Extended
Reason: I can understand you want to be paid. So I will commit to the fee but I want you to have time to make a KICK ASS website for me dudes! Thanks

HI!  Just wanted to say thanks for your time on these.  A lot are great.  However the firefighters have nothing to do with Foreclosure.  We are saving peoples homes from the bank taking them and selling them.   I LOVE the house photos and the families on the website.  That is the direction we like.  THanks.

THANK U ALL FOR THE WORK!   I like a few ending in the numbers: 147  733  693  536  620  478  727  508     I will go over them and choose one soon.  Thank you.   You will be paid shortly. 

Requirements
Must have
• Bright, Upbeat photos. Color scheme should be in order. We like icons on the bottom. not just text.

```html
<!DOCTYPE html>
<html lang="en">
<head>
<meta charset="utf-8">
<title>Hearthside Lending Relief</title>
<link href="https://fonts.googleapis.com/css2?family=Arimo:wght@400;700&display=swap" rel="stylesheet">
<style>
  :root{
    --brand-red:#d91f26;
    --nav-red:#d8262c;
    --ink:#111111;
    --panel-light:#f4f4f4;
    --white:#ffffff;
    --footer-black:#050505;
    --sky:#a9c3dc;
    --brick:#9a8674;
    --lawn:#4f6b2c;
  }
  *{margin:0;padding:0;box-sizing:border-box}
  html,body{width:1200px;height:1010px;overflow:hidden;background:var(--white)}
  body{font-family:"Arimo",Arial,sans-serif;color:var(--ink)}
  .page{position:relative;width:1200px;height:1010px;overflow:hidden;background:var(--brand-red)}

  .site-header{position:absolute;left:0;top:0;width:1200px;height:67px;
    background:linear-gradient(90deg,#f6f6f6 0%,#ececec 60%,#e4e4e4 100%)}
  .main-nav a{position:absolute;top:29px;font-weight:700;font-size:14px;text-decoration:none;color:var(--nav-red);white-space:nowrap}
  .main-nav a.is-active{color:var(--ink)}
  .nav-marker{position:absolute;left:524px;top:61px}

  .logo-card{position:absolute;left:100px;top:0;width:314px;height:176px;z-index:3}
  .logo-mark{position:absolute;left:24px;top:37px;width:70px;height:70px;border-radius:50%;background:var(--brand-red)}
  .logo-name{position:absolute;left:104px;top:44px;font-weight:700;font-size:19px;line-height:20px;color:var(--ink);letter-spacing:.4px}

  .hero{position:absolute;left:0;top:67px;width:854px;height:540px;
    background:
      radial-gradient(ellipse 300px 260px at 640px 300px,rgba(120,95,80,.55),rgba(120,95,80,0) 70%),
      radial-gradient(ellipse 280px 200px at 300px 280px,rgba(160,140,120,.75),rgba(160,140,120,0) 75%),
      linear-gradient(180deg,#8fb3d6 0%,var(--sky) 22%,#c9ccc6 38%,var(--brick) 56%,#6f7d48 74%,var(--lawn) 86%,#3c4a22 100%)}
  .hero-caption{position:absolute;left:0;bottom:0;width:854px;height:85px;
    background:linear-gradient(90deg,rgba(30,30,30,.78),rgba(30,30,30,.6) 70%,rgba(30,30,30,.4))}
  .hero-caption p{position:absolute;left:112px;top:21px;color:var(--white);font-weight:700;font-size:19px;line-height:24px}

  .side-panel{position:absolute;left:854px;top:67px;width:346px;height:540px;
    background:linear-gradient(90deg,#ececec 0%,var(--panel-light) 40%,#fafafa 100%)}
  .side-photo{position:absolute;left:16px;width:220px;height:144px;border-radius:7px;background:var(--brand-red);padding:5px 2px 8px}
  .side-photo .photo-fill{width:100%;height:100%;border-radius:4px}
  .photo-couple .photo-fill{background:
      radial-gradient(ellipse 60px 70px at 95px 80px,rgba(110,110,105,.8),rgba(110,110,105,0) 75%),
      linear-gradient(90deg,#d9d2ae 0%,#a9a77c 30%,#e9dcb0 65%,#f3f1e8 100%)}
  .photo-family .photo-fill{background:
      radial-gradient(ellipse 110px 60px at 108px 95px,rgba(70,60,75,.7),rgba(70,60,75,0) 80%),
      linear-gradient(180deg,#b8c8dc 0%,#d2b59c 45%,#6e6472 100%)}

  .contact-block{position:absolute;right:128px;top:365px;text-align:right}
  .call-label{display:flex;justify-content:flex-end;align-items:center;gap:1px;color:var(--brand-red);font-weight:700;font-size:22px}
  .call-number{font-weight:700;font-size:24px;color:var(--ink);margin-top:1px;letter-spacing:.3px}
  .call-rule{margin-top:5px;margin-left:auto;width:157px;height:1px;background:var(--ink)}
  .office{margin-top:19px;font-size:12px;font-weight:700;line-height:18px}
  .office .office-name{color:var(--brand-red)}

  .welcome{position:absolute;left:119px;top:619px;width:961px;color:var(--white)}
  .welcome h1{font-size:22px;font-weight:700;padding-left:2px;padding-bottom:8px;border-bottom:1px solid #5a1012}
  .welcome .copy{margin-top:6px;font-size:12px;line-height:18px;width:985px}
  .welcome .copy p.spaced{margin-top:18px}

  .footer-swoosh{position:absolute;left:0;top:945px}
  .footer-links a{position:absolute;top:985px;font-size:12px;color:var(--white);text-decoration:none;white-space:nowrap}
  .copyright{position:absolute;right:114px;top:985px;font-size:12px;color:var(--white)}
</style>
</head>
<body>
<div class="page">

  <header class="site-header">
    <nav class="main-nav">
      <a class="is-active" href="#" style="left:520px">HOME</a>
      <a href="#" style="left:597px">ABOUT US</a>
      <a href="#" style="left:697px">SERVICES</a>
      <a href="#" style="left:795px">FINANCING OPTIONS</a>
      <a href="#" style="left:967px">CONTACT US</a>
    </nav>
    <svg class="nav-marker" width="30" height="6" viewBox="0 0 30 6"><path d="M0 6 L15 0 L30 6Z" fill="var(--brand-red)"/></svg>
  </header>

  <div class="logo-card">
    <svg width="314" height="176" viewBox="0 0 314 176" style="position:absolute;left:0;top:0">
      <defs>
        <linearGradient id="cardFill" x1="0" y1="0" x2="0" y2="1">
          <stop offset="0" stop-color="#ffffff"/><stop offset="1" stop-color="#ececec"/>
        </linearGradient>
      </defs>
      <path d="M0 0 H314 V140 L157 174 L0 140Z" fill="url(#cardFill)" stroke="#d6d6d6"/>
    </svg>
    <span class="logo-mark"></span>
    <div class="logo-name">HEARTHSIDE<br>LENDING<br>RELIEF</div>
  </div>

  <section class="hero" role="img" aria-label="Smiling family of four posing on the lawn in front of a large brick house under a blue sky">
    <div class="hero-caption">
      <p>Offering solid alternatives<br>to losing your home in a Trustee Sale</p>
    </div>
  </section>

  <aside class="side-panel">
    <div class="side-photo photo-couple" style="top:30px">
      <div class="photo-fill" role="img" aria-label="Couple embracing while looking at a new home"></div>
    </div>
    <div class="side-photo photo-family" style="top:190px">
      <div class="photo-fill" role="img" aria-label="Happy family group standing together outdoors"></div>
    </div>

    <div class="contact-block">
      <div class="call-label">
        <svg width="18" height="24" viewBox="0 0 18 24"><path d="M5 2 C2 3 1 7 2 11 C4 17 8 21 13 22 C15 22 16 21 17 19 L13 15 L10 17 C8 15 6 12 6 9 L9 7 Z" fill="none" stroke="var(--brand-red)" stroke-width="2.2" stroke-linejoin="round"/></svg>
        <span>Call Us</span>
      </div>
      <div class="call-number">877-555-0142</div>
      <div class="call-rule"></div>
      <div class="office">
        <div class="office-name">HEARTHSIDE LENDING RELIEF</div>
        <div>218 Harbor Crest Ave, Suite 310</div>
        <div>Bayfield, CA 92000</div>
      </div>
    </div>
  </aside>

  <main class="welcome">
    <h1>Welcome to Hearthside Lending Relief</h1>
    <div class="copy">
      <p>HEARTHSIDE LENDING RELIEF specializes in assisting homeowners who are in FORECLOSURE, by offering solid alternatives to losing your home in a Trustee Sale.&nbsp; Having your home foreclosed on can damage your credit for up to 7 years.&nbsp; Most foreclosures end with the home owner being evicted from their home, leaving them with no money, no place to live and without ample time to safely aremove their possessions from their home.&nbsp; There is no need to have this happen to you.&nbsp; No matter what part of foreclosure process you are in, WE CAN HELP!</p>
      <p>If you have received a Notice of Default (NOD) or Notice of Trustee Sale (NTS), you have options.&nbsp; Contact us today to speak to one of our licensed specialist, and let us help you put this situation behind you.</p>
      <p class="spaced">We speak to hundreds of homeowners every day, we understand how frustrating this can be.&nbsp; Don't live in fear of what is to come.&nbsp; You have other options, please call or email us today and we will immediately put our specialist to work finding you a solution.</p>
      <p class="spaced">Don't try to handle this frustrating situation by yourself.&nbsp; HEARTHSIDE LENDING RELIEF is a team of knowledgeable real estate professionals, we can offer you a better solution during this tough time.</p>
      <p class="spaced">HEARTHSIDE LENDING RELIEF&nbsp; has been assisting families in foreclosure for years.&nbsp; Our skill and integrity has earned us a reputation for fast, professional, courteous and thorough solutions.&nbsp; With over 50 years of real estate knowledge and experience HEARTHSIDE LENDING RELIEF is ready to assist you.</p>
    </div>
  </main>

  <svg class="footer-swoosh" width="1200" height="65" viewBox="0 0 1200 65">
    <path d="M0 32 Q520 8 1200 22 L1200 65 L0 65Z" fill="var(--footer-black)"/>
    <path d="M0 36 Q480 2 1200 14 L1200 20 Q560 6 0 44Z" fill="var(--white)"/>
  </svg>
  <nav class="footer-links">
    <a href="#" style="left:109px">Home</a>
    <a href="#" style="left:170px">About Us</a>
    <a href="#" style="left:241px">Services</a>
    <a href="#" style="left:309px">Financing Options</a>
    <a href="#" style="left:430px">Contact Us</a>
  </nav>
  <div class="copyright">Content copyright 2012. HEARTHSIDELENDINGRELIEF.COM. All rights reserved.</div>

</div>
</body>
</html>
```